New career and executive coaching business needs a business card design including logo

Company name: 'Bramblefield Growth Partners.' The aim of my coaching engagements is to help people improve their communication in the workplace and achieve their career goals. The process involves working with individuals to help them uncover their strengths and talents, then leverage those to improve their working lives. The Tarwick Inventory is the starting point to the process. I am after an exciting and interesting business card design (including logo)which is professional yet will still get people's attention.

Industry/Entity Type

Business

Contact Information for Business Card

Name: Malcolm Dervaney
Position: Owner
Address: 58 Quorrin Ct, Elmbridge Vic 3190
Phone: 0418923047
Website: bramblefieldgrowth.com.au
Email: malcolm@bgp.com.au

Colors
33a6d7
00a990
0355a3
3176b5

Requirements
Must have
• logo

```html
<!DOCTYPE html>
<html lang="en">
<head>
<meta charset="utf-8">
<title>Bramblefield Growth Partners – Business Cards</title>
<link rel="stylesheet" href="https://fonts.googleapis.com/css2?family=Oswald:wght@500&family=Open+Sans:wght@400;700&display=swap">
<style>
  :root {
    --sky: #33a6d7;
    --teal: #00a990;
    --navy: #0355a3;
    --blue: #3176b5;
    --card: #0d0d0d;
    --ring: #b9b9b9;
    --ink: #e8e8e8;
    --muted: #cfcfcf;
    --backdrop: #4a4540;
  }
  * { box-sizing: border-box; margin: 0; padding: 0; }
  html, body { width: 1200px; height: 900px; overflow: hidden; }
  body {
    background: var(--backdrop);
    font-family: "Open Sans", Arial, sans-serif;
    position: relative;
  }
  .card {
    position: absolute;
    width: 530px;
    height: 310px;
    background: var(--card);
    border-radius: 4px;
  }
  /* Contact side */
  .card-contact { left: 45px; top: 400px; }
  .contact-mark {
    position: absolute;
    left: 55px; top: 70px;
    width: 170px;
    text-align: center;
  }
  .mark-circle {
    width: 150px; height: 150px;
    margin: 0 auto;
    border-radius: 50%;
    background: var(--blue);
    border: 4px solid var(--ring);
  }
  .mark-name {
    margin-top: 12px;
    font-size: 13px;
    font-weight: 700;
    color: var(--blue);
    line-height: 1.3;
  }
  .contact-details {
    position: absolute;
    left: 275px; top: 62px;
    padding-left: 16px;
    border-left: 1px solid #1f3b36;
    height: 190px;
  }
  .person-name { color: var(--teal); font-weight: 700; font-size: 17px; line-height: 1.2; }
  .person-role { color: var(--muted); font-size: 13px; margin-bottom: 20px; }
  .address { color: var(--ink); font-size: 14px; line-height: 1.45; margin-bottom: 18px; }
  .contact-list { list-style: none; }
  .contact-list li {
    display: flex; align-items: center; gap: 8px;
    color: var(--ink); font-size: 14px; line-height: 1.5;
  }
  .contact-list svg { width: 11px; height: 11px; flex: none; }
  /* Brand side */
  .card-brand { left: 625px; top: 150px; }
  .brand-lockup {
    position: absolute;
    left: 60px; top: 105px;
    display: flex; align-items: center; gap: 22px;
  }
  .brand-circle {
    width: 100px; height: 100px;
    border-radius: 50%;
    background: var(--blue);
    border: 3px solid var(--ring);
    flex: none;
  }
  .brand-name {
    font-family: "Oswald", "Arial Narrow", sans-serif;
    font-weight: 500;
    font-size: 30px;
    line-height: 1.1;
    text-transform: uppercase;
    color: var(--blue);
  }
</style>
</head>
<body>
  <section class="card card-contact">
    <div class="contact-mark">
      <div class="mark-circle"></div>
      <p class="mark-name">Bramblefield Growth Partners</p>
    </div>
    <div class="contact-details">
      <p class="person-name">Malcolm Dervaney</p>
      <p class="person-role">Owner</p>
      <p class="address">58 Quorrin Ct, Elmbridge<br>Vic 3190</p>
      <ul class="contact-list">
        <li>
          <svg viewBox="0 0 12 12" aria-hidden="true"><path fill="var(--teal)" d="M2.5 0.5l2 2.5-1.2 1.3c.7 1.6 2 2.9 3.6 3.6L8.2 6.7l2.5 2-1.3 2.3C5 11 1 7 0.5 2.6z"/></svg>
          0418923047
        </li>
        <li>
          <svg viewBox="0 0 12 12" aria-hidden="true"><rect x="0.5" y="2" width="11" height="8" fill="var(--teal)"/><path d="M0.5 2l5.5 4.5L11.5 2" fill="none" stroke="var(--card)" stroke-width="1"/></svg>
          malcolm@bgp.com.au
        </li>
        <li>
          <svg viewBox="0 0 12 12" aria-hidden="true"><circle cx="6" cy="6" r="5.5" fill="var(--teal)"/><path d="M0.5 6h11M6 0.5c-2.5 3-2.5 8 0 11M6 0.5c2.5 3 2.5 8 0 11" fill="none" stroke="var(--card)" stroke-width="0.8"/></svg>
          bramblefieldgrowth.com.au
        </li>
      </ul>
    </div>
  </section>

  <section class="card card-brand">
    <div class="brand-lockup">
      <div class="brand-circle"></div>
      <p class="brand-name">Bramblefield<br>Growth Partners</p>
    </div>
  </section>
</body>
</html>
```